Business Card Design for Flood Rescue 360 - Property Restoration Professionals

I need a business card designed for Flood Rescue 360. We are a full-service property restoration solution. Providing water, fire, smoke & storm restoration as well as mold remediation and full remodel or reconstruction to homes and businesses across Dallas-Fort Worth, TX.
Target Market(s)
home and business owners with insurance covered property damage from water, fire or storm related damage
Industry/Entity Type
property restoration
Contact Information for Business Card
Marcus Pelley General Manager Cell: 214-555-0193 Office: 469-555-0148 email: Marcus@FloodRescue360.example services: Water, Fire, Mold, Reconstruction Tagline: Urgency for Your Water Emergency!
Look and feel
Each slider illustrates characteristics of the customer's brand and the style your logo design should communicate.

```html
<!DOCTYPE html>
<html lang="en">
<head>
<meta charset="utf-8">
<title>Flood Rescue 360 – Business Card</title>
<link rel="stylesheet" href="https://fonts.googleapis.com/css2?family=Roboto:wght@400;500;700;900&display=swap">
<style>
  :root {
    --brand-blue: #19b3e6;
    --brand-grey: #7c7c7c;
    --ink: #1d1d1d;
    --card: #f1f1f1;
    --backdrop: #d4d8d8;
    --faint: #e4e4e4;
  }
  * { box-sizing: border-box; margin: 0; padding: 0; }
  html, body { width: 1200px; height: 960px; overflow: hidden; }
  body {
    background: var(--backdrop);
    font-family: "Roboto", Arial, sans-serif;
    position: relative;
  }
  .card {
    position: absolute;
    left: 250px;
    width: 700px;
    height: 400px;
    background: var(--card);
    border-radius: 30px;
    overflow: hidden;
  }
  .card--front { top: 60px; }
  .card--back { top: 500px; }

  .brand {
    position: absolute;
    display: flex;
    align-items: center;
    gap: 18px;
    color: var(--brand-blue);
    font-weight: 900;
    text-transform: uppercase;
    line-height: 0.9;
  }
  .brand__dot {
    flex: none;
    border-radius: 50%;
    background: var(--brand-blue);
  }
  .card--front .brand { left: 155px; top: 140px; font-size: 58px; }
  .card--front .brand__dot { width: 100px; height: 100px; }
  .card--back .brand { left: 28px; top: 32px; font-size: 44px; }
  .card--back .brand__dot { width: 84px; height: 84px; }

  .services {
    position: absolute;
    left: 0; right: 0; top: 332px;
    text-align: center;
  }
  .services__heading {
    display: flex;
    align-items: center;
    justify-content: center;
    gap: 8px;
    color: var(--brand-blue);
    font-weight: 500;
    font-size: 17px;
  }
  .services__rule {
    width: 122px;
    height: 2px;
    background: var(--brand-blue);
  }
  .services__list {
    display: flex;
    justify-content: center;
    gap: 10px;
    list-style: none;
    margin-top: 6px;
    font-size: 18px;
    color: var(--ink);
  }
  .services__list li { display: flex; align-items: center; gap: 7px; }
  .services__list li::before {
    content: "";
    width: 10px; height: 10px;
    border-radius: 50%;
    border: 2px solid var(--brand-blue);
  }

  .person {
    position: absolute;
    right: 28px;
    top: 24px;
    text-align: right;
  }
  .person__name {
    font-size: 38px;
    font-weight: 500;
    line-height: 1.1;
    color: var(--brand-blue);
  }
  .person__name .surname { color: var(--brand-grey); font-weight: 400; }
  .person__title { font-size: 17px; font-weight: 500; color: var(--ink); }
  .accent-bar {
    position: absolute;
    right: 0; top: 31px;
    width: 19px; height: 61px;
    background: var(--brand-blue);
  }

  .tagline {
    position: absolute;
    left: 25px; top: 248px;
    font-size: 17px;
    font-weight: 500;
    color: var(--brand-blue);
  }
  .contact {
    position: absolute;
    left: 28px; top: 310px;
    list-style: none;
    font-size: 17px;
    color: var(--ink);
    letter-spacing: 0.5px;
  }
  .contact li { display: flex; align-items: center; gap: 12px; height: 24px; }
  .contact svg { width: 16px; height: 16px; flex: none; }

  .seal {
    position: absolute;
    left: 478px; top: 168px;
    width: 224px; height: 224px;
    border-radius: 50%;
    border: 10px solid var(--faint);
  }
</style>
</head>
<body>
  <section class="card card--front" aria-label="Card front">
    <div class="brand">
      <span>Flood<br>Rescue<br>360</span>
      <span class="brand__dot"></span>
    </div>
    <div class="services">
      <div class="services__heading">
        <span class="services__rule"></span>SERVICES<span class="services__rule"></span>
      </div>
      <ul class="services__list">
        <li>Water</li><li>Fire</li><li>Mold</li><li>Reconstruction</li>
      </ul>
    </div>
  </section>

  <section class="card card--back" aria-label="Card back">
    <div class="brand">
      <span>Flood<br>Rescue<br>360</span>
      <span class="brand__dot"></span>
    </div>
    <div class="person">
      <p class="person__name">Marcus <span class="surname">Pelley</span></p>
      <p class="person__title">General Manager</p>
    </div>
    <span class="accent-bar"></span>
    <span class="seal" aria-hidden="true"></span>
    <p class="tagline">Urgency for Your Water Emergency!</p>
    <ul class="contact">
      <li>
        <svg viewBox="0 0 16 16" aria-hidden="true"><rect x="4" y="1" width="8" height="14" rx="1.5" fill="none" stroke="#19b3e6" stroke-width="1.5"/><line x1="7" y1="12.5" x2="9" y2="12.5" stroke="#19b3e6" stroke-width="1.2"/></svg>
        214-555-0193
      </li>
      <li>
        <svg viewBox="0 0 16 16" aria-hidden="true"><path d="M3 2l3 0 1 3-2 1.5c1 2 2.5 3.5 4.5 4.5L11 9l3 1v3c-6 1-12-5-11-11z" fill="#19b3e6"/></svg>
        469-555-0148
      </li>
      <li>
        <svg viewBox="0 0 16 16" aria-hidden="true"><rect x="1" y="4" width="14" height="10" rx="1" fill="#19b3e6"/><path d="M1 4l7 6 7-6" fill="none" stroke="#f1f1f1" stroke-width="1.3"/></svg>
        Marcus@FloodRescue360.example
      </li>
    </ul>
  </section>
</body>
</html>
```